Boutique custom software development company needs new business card

Our nearly 20 year old custom software development company would like to better include the fact that we are now providing Bitcoin services. These new services are B2B include education (how to acquire and securely hold Bitcoin) and integrating Bitcoin payments into existing ecommerce sites or other existing systems. Please keep the card clean and simple. Attached is our current design and some other files. vextorial.com

Target Market(s)

businesses owners interested in long term relationship

Industry/Entity Type

Custom software development and Bitcoin

Contact Information for Business Card

Dale Parker, dale@vextorial.com, vextorial.com, (888) 555-VXTRL

Font styles to use
Other font styles liked:
• monospace

Requirements
Must have
• double-sided
Nice to have
• clean and simple
Should not have
• physical address

```html
<!DOCTYPE html>
<html lang="en">
<head>
<meta charset="utf-8">
<title>Vextorial – Business Card</title>
<link href="https://fonts.googleapis.com/css2?family=Archivo:wght@800&family=Arimo:wght@400&family=Lato:wght@400&display=swap" rel="stylesheet">
<style>
  :root {
    --bg: #e9eaec;
    --brand-blue: #2f5f9e;
    --brand-orange: #e06b1f;
    --paper: #f1f1ef;
    --white: #ffffff;
    --tagline: #d9dde4;
  }
  * { box-sizing: border-box; margin: 0; padding: 0; }
  html, body {
    width: 1200px; height: 874px; overflow: hidden;
    background: var(--bg);
  }
  .canvas { position: relative; width: 1200px; height: 874px; }
  .card {
    position: absolute; left: 280px; width: 640px; height: 366px;
    box-shadow: 0 6px 18px rgba(0,0,0,.18);
    overflow: hidden;
  }
  .card--front { top: 56px; background: var(--brand-blue); }
  .card--back { top: 452px; background: var(--brand-blue); display: flex; }

  /* front */
  .front-brand {
    position: absolute; left: 0; right: 0; top: 112px;
    display: flex; flex-direction: column; align-items: center;
  }
  .wordmark { display: flex; align-items: center; gap: 14px; }
  .wordmark__square { width: 34px; height: 34px; background: var(--brand-orange); }
  .wordmark__name {
    font-family: "Archivo", sans-serif; font-weight: 800;
    font-size: 62px; letter-spacing: 1px; color: var(--white);
    line-height: 1; text-transform: uppercase;
  }
  .tagline {
    margin-top: 14px;
    font-family: "Lato", sans-serif; font-size: 22px;
    color: var(--tagline); letter-spacing: .2px;
  }
  .services {
    margin-top: 22px; padding-top: 14px;
    border-top: 2px solid var(--brand-orange);
    font-family: "Lato", sans-serif; font-size: 17px;
    color: var(--white); letter-spacing: .3px;
  }

  /* back */
  .back-logo {
    width: 282px; height: 100%; background: var(--paper);
    display: flex; align-items: center; justify-content: center;
    border-right: 4px solid var(--brand-orange);
  }
  .back-logo .wordmark { gap: 10px; }
  .back-logo .wordmark__square { width: 22px; height: 22px; }
  .back-logo .wordmark__name { font-size: 34px; color: var(--brand-blue); }
  .back-info { flex: 1; padding: 84px 0 0 86px; color: var(--white); }
  .person-name {
    font-family: "Archivo", sans-serif; font-weight: 800;
    font-size: 23px; letter-spacing: 1.5px; text-transform: uppercase;
    margin-bottom: 26px;
  }
  .contact-list { list-style: none; }
  .contact-item {
    display: flex; align-items: center; gap: 8px;
    font-family: "Arimo", sans-serif; font-size: 19px; line-height: 26px;
  }
  .contact-icon { width: 17px; height: 17px; flex: none; }
  .back-services {
    margin-top: 22px;
    font-family: "Lato", sans-serif; font-size: 15px; line-height: 20px;
    color: var(--tagline);
  }
</style>
</head>
<body>
<div class="canvas">

  <section class="card card--front" aria-label="Card front">
    <div class="front-brand">
      <div class="wordmark">
        <span class="wordmark__square"></span>
        <span class="wordmark__name">Vextorial</span>
      </div>
      <p class="tagline">developer of custom applications</p>
      <p class="services">Bitcoin education &amp; payment integration for business</p>
    </div>
  </section>

  <section class="card card--back" aria-label="Card back">
    <div class="back-logo">
      <div class="wordmark">
        <span class="wordmark__square"></span>
        <span class="wordmark__name">Vextorial</span>
      </div>
    </div>
    <div class="back-info">
      <h1 class="person-name">Dale Parker</h1>
      <ul class="contact-list">
        <li class="contact-item">
          <svg class="contact-icon" viewBox="0 0 18 18" aria-hidden="true">
            <rect width="18" height="18" fill="#f1f1ef"/>
            <path d="M5 3.5l2.2 0 .9 3-1.4 1.1c.7 1.5 1.8 2.6 3.2 3.2l1.1-1.4 3 .9 0 2.2c-5.3.4-9.4-3.7-9-9z" fill="#e06b1f"/>
          </svg>
          (888) 555-VXTRL
        </li>
        <li class="contact-item">
          <svg class="contact-icon" viewBox="0 0 18 18" aria-hidden="true">
            <rect width="18" height="18" fill="#f1f1ef"/>
            <rect x="3" y="5" width="12" height="8" fill="#e06b1f"/>
            <path d="M3 5l6 5 6-5" fill="none" stroke="#f1f1ef" stroke-width="1.2"/>
          </svg>
          dale@vextorial.com
        </li>
        <li class="contact-item">
          <svg class="contact-icon" viewBox="0 0 18 18" aria-hidden="true">
            <rect width="18" height="18" fill="#f1f1ef"/>
            <circle cx="9" cy="9" r="5.5" fill="#e06b1f"/>
            <path d="M3.5 9h11M9 3.5c-2 2.5-2 8.5 0 11M9 3.5c2 2.5 2 8.5 0 11" fill="none" stroke="#f1f1ef" stroke-width=".9"/>
          </svg>
          www.vextorial.com
        </li>
      </ul>
      <p class="back-services">Custom software · Bitcoin services</p>
    </div>
  </section>

</div>
</body>
</html>
```